Dental Practice Website design

Design a new website for Brambleford Dental Practice.
Design should be warm, neutral in colour, with some small amount of bright colour if needed but kept to a minimum. Website should look professional, high end. Home page should be easy to navigate and simple for patients to be able to book online.
Logo in files along with some examples of websites that we like. Please ask if any further info needed.
Menu should have:
About
New Patients
Treatments
Fees
Contact Us

Industry/Entity Type

Dentistry

Number of Pages Required

4 page

Font styles to use
Sans Serif

Colors

Designer to choose colors to be used in the design.

Requirements
Must have
• Ravelle ratings badge, book online button,
Nice to have
• neutral, relaxing colours
Should not have
• harsh, bright colours!

```html
<!DOCTYPE html>
<html lang="en">
<head>
<meta charset="utf-8">
<title>Brambleford Dental Practice</title>
<link href="https://fonts.googleapis.com/css2?family=Bricolage+Grotesque:wght@500;700;800&family=Outfit:wght@300;400;500;600&display=swap" rel="stylesheet">
<style>
:root{
  --navy:#1b2a4e;
  --brand-blue:#1a5fa8;
  --tan:#a99a86;
  --tan-dark:#8f7f6a;
  --cream:#fdf8f1;
  --ink:#2b2b2b;
  --muted:#555;
  --brown:#3a2a1e;
  --sky:#bdecf7;
  --card-yellow:#fdf0c4;
  --card-peach:#fde3da;
  --card-mint:#dff4e6;
  --white:#fff;
}
*{box-sizing:border-box;margin:0;padding:0}
html,body{width:1200px;height:3979px;overflow:hidden}
body{font-family:"Outfit",sans-serif;color:var(--ink);background:var(--white);position:relative}
.abs{position:absolute}
h1,h2,h3{font-family:"Bricolage Grotesque",sans-serif}
.btn{display:inline-block;font-family:"Outfit",sans-serif;font-size:12px;color:#fff;background:var(--tan);padding:9px 18px;border-radius:2px;text-decoration:none}
.btn-navy{background:var(--navy)}

/* top bar & nav */
.topbar{left:0;top:0;width:1200px;height:27px;background:var(--navy);color:#c9d3e8;font-size:10px;display:flex;justify-content:flex-end;align-items:center;gap:34px;padding-right:156px}
.topbar span{display:flex;align-items:center;gap:5px}
.nav{left:0;top:27px;width:1200px;height:61px;background:#fff}
.logo{left:156px;top:0;width:154px;height:116px;background:var(--brand-blue);color:#cfe0f5;display:flex;flex-direction:column;align-items:center;justify-content:flex-end;padding-bottom:14px;z-index:3;text-align:center}
.logo .name{font-family:"Outfit",sans-serif;font-weight:300;font-size:17px;letter-spacing:1px;line-height:1.2}
.logo .sub{font-size:11px;letter-spacing:1px}
.menu{left:450px;top:27px;height:61px;display:flex;align-items:center;gap:22px;font-size:11.5px;color:var(--ink)}
.menu .active{color:var(--brand-blue);text-decoration:underline}
.nav-cta{left:880px;top:40px;width:164px;height:34px;background:var(--tan);color:#fff;font-size:12px;display:flex;align-items:center;justify-content:center;border-radius:2px}

/* hero */
.hero{left:0;top:88px;width:1200px;height:499px;background:linear-gradient(90deg,#5a4a3c 0%,#8b6f58 45%,#c9a58b 75%,#b98a6c 100%)}
.hero-text{left:156px;top:240px;color:#fff}
.hero-text h1{font-size:43px;font-weight:800;line-height:1.15}
.hero-text p{font-size:10px;margin:12px 0 18px}
.badge{left:888px;top:543px;width:154px;height:62px;background:#fff;border-radius:4px;box-shadow:0 2px 8px rgba(0,0,0,.18);display:flex;align-items:center;gap:8px;padding:0 12px;white-space:nowrap}
.badge .sq{width:30px;height:30px;border:1px solid #ccc;border-radius:4px;flex:none}
.badge .lbl{font-size:10px;color:#666;display:block;line-height:1.2}
.badge .row{display:flex;align-items:center;gap:4px}
.badge b{font-size:17px;color:#333;line-height:1}
.badge .meta{display:flex;flex-direction:column;line-height:1.1}
.badge .stars{color:#f4b400;font-size:7px}
.badge .count{font-size:8.5px;color:#666}

/* welcome */
.ph{background:linear-gradient(135deg,#e9e2da,#cdbfb1)}
.welcome-h{left:664px;top:716px;font-size:30px;line-height:1.25}
.welcome-h .thin{font-family:"Outfit",sans-serif;font-weight:400;color:var(--tan)}
.welcome-h .bold{font-weight:700;color:var(--tan)}
.copy{font-size:10.5px;line-height:1.55;color:var(--muted)}
.copy p+p{margin-top:15px}

/* join */
.join{left:0;top:1248px;width:1200px;height:558px;background:var(--cream)}
.section-title{font-size:31px;font-weight:700;color:var(--tan)}

/* treatments */
.card{width:280px;height:195px;padding:24px 26px}
.card svg{display:block;margin-bottom:18px}
.card h3{font-size:15px;font-weight:600;color:var(--ink);margin-bottom:7px}
.card p{font-size:10.5px;line-height:1.55;color:var(--tan-dark)}
.yellow{background:var(--card-yellow)}.peach{background:var(--card-peach)}.mint{background:var(--card-mint)}

/* testimonial */
.testi{left:335px;top:2517px;width:865px;height:398px;background:var(--navy);color:#fff;padding:75px 0 0 103px}
.testi h2{font-size:31px;color:var(--tan);font-weight:700;margin-bottom:24px}
.testi p{font-size:16px;line-height:1.5;font-weight:300;width:580px;color:#e6eaf3}
.author{display:flex;align-items:center;gap:12px;margin-top:30px}
.avatar{width:44px;height:44px;border-radius:50%;background:#c9b5a2;border:2px solid #fff}
.author b{font-size:12px;color:var(--tan);display:block}
.author small{font-size:9px}
.dots{display:flex;gap:6px;margin-left:64px}
.dots i{width:10px;height:10px;border-radius:50%;border:1px solid #fff;display:block}
.dots i.on{border-color:var(--tan);background:radial-gradient(var(--tan) 35%,transparent 40%)}
.quote-box{left:926px;top:2455px;width:116px;height:113px;background:var(--sky);display:flex;align-items:center;justify-content:center}

/* team */
.team-card{width:173px;height:255px;background:#fff;box-shadow:0 2px 10px rgba(0,0,0,.08)}
.team-card .ph{height:168px;background:linear-gradient(160deg,#d6e6ec,#9fbccc)}
.team-card .info{padding:10px 12px}
.team-card small{font-size:8.5px;color:#999}
.team-card h3{font-family:"Outfit",sans-serif;font-size:12px;font-weight:500;margin:2px 0 3px;white-space:nowrap}
.team-card p{font-size:9px;color:var(--tan-dark);line-height:1.4}

/* footer */
.map{left:0;top:3324px;width:1200px;height:369px;background:linear-gradient(90deg,#9fd3e6 0%,#cfe8d3 20%,#d8ecd4 60%,#a7d8e9 85%)}
.footer{left:0;top:3693px;width:1200px;height:241px;background:var(--brown);color:#e7ddd2}
.footer h4{font-size:13px;font-weight:500;color:var(--tan);margin-bottom:14px}
.footer .col{top:47px;font-size:10.5px;line-height:1.8}
.footer-logo{left:156px;top:58px;width:160px;color:#d9cbbb;text-align:center;font-weight:300;font-size:20px;letter-spacing:1px;line-height:1.2}
.footer-logo .sub{font-size:13px}
.footer .hours td{padding-right:32px}
.bottombar{left:0;top:3934px;width:1200px;height:45px;background:var(--navy);color:#d6dcea;font-size:10px;display:flex;align-items:center;justify-content:space-between;padding:0 156px}
.social{display:flex;gap:6px}
.social i{width:20px;height:20px;border-radius:50%;border:1px solid #d6dcea;display:block}
</style>
</head>
<body>

<div class="abs topbar">
  <span><svg width="9" height="11" viewBox="0 0 10 12"><path d="M5 0a4 4 0 0 1 4 4c0 3-4 8-4 8S1 7 1 4a4 4 0 0 1 4-4z" fill="#6fa6e0"/></svg>Lorem Ipsum 1, 40217 Elmsworth</span>
  <span><svg width="10" height="10" viewBox="0 0 10 10"><path d="M2 0l2 2-1 2 3 3 2-1 2 2-2 2C4 10 0 6 0 2z" fill="#6fa6e0"/></svg>555-014-2290</span>
  <span><svg width="10" height="10" viewBox="0 0 10 10"><circle cx="5" cy="5" r="5" fill="#6fa6e0"/></svg>Mon - Fri: 9am - 5pm</span>
</div>
<div class="abs nav"></div>
<div class="abs logo"><div class="name">BRAMBLEFORD<br><span class="sub">DENTAL PRACTICE</span></div></div>
<nav class="abs menu">
  <span class="active">Home</span><span>About Us</span><span>New Patients</span><span>Treatments</span><span>Fees</span><span>Contact Us</span>
</nav>
<div class="abs nav-cta">Book An Appointment</div>

<section class="abs hero" role="img" aria-label="Smiling patient in a dental chair during a check-up"></section>
<div class="abs hero-text">
  <h1>Your Best<br>Dental Experience</h1>
  <p>Lorem Ipsum Is Simply Dummy Text Of The Printing And Typesetting Industry.</p>
  <span class="btn btn-navy">Book An Appointment</span>
</div>
<div class="abs badge"><div class="sq"></div><div><span class="lbl">Ravelle Ratings</span><div class="row"><b>4.9</b><span class="meta"><span class="stars">★★★★★</span><span class="count">152 reviews</span></span></div></div></div>

<div class="abs ph" style="left:156px;top:664px;width:406px;height:451px;border:1px solid #ddd" role="img" aria-label="Dentist examining a smiling patient"></div>
<div class="abs ph" style="left:329px;top:911px;width:253px;height:250px;border:4px solid #fff;background:linear-gradient(135deg,#c7dfe4,#7fb3c0)" role="img" aria-label="Smiling male patient in dental chair"></div>
<h2 class="abs welcome-h"><span class="thin">Welcome To</span><br><span class="bold">Our Friendly Dental<br>Practice</span></h2>
<div class="abs copy" style="left:664px;top:845px;width:378px">
  <p>Nestled In The Heart Of Beautiful Hollowmere, UK. Our Team Of Dedicated Dentists, Hygienists And Support Staff Are Here To Provide You With Exceptional Dental Care. With A Wide Array Of Services, Including General And Cosmetic Dentistry, Orthodontics And Emergency Care, We're Confident That We Can Deliver The Highest Quality Treatment To You And Your Loved Ones.</p>
  <p>At Our Practice, We Believe That A Visit To The Dentist Should Be A Comfortable And Positive Experience. We Strive To Create A Warm And Welcoming Atmosphere Where Our Patients Can Feel At Ease And Confident In The Care They Receive. Our State-Of-The-Art Facilities And Equipment Mean That You Can Trust Us To Deliver The Latest Techniques And Treatments To Ensure Your Oral Health Is At Its Best.</p>
</div>
<span class="abs btn" style="left:664px;top:1077px">Read More</span>

<section class="abs join"></section>
<h2 class="abs section-title" style="left:156px;top:1368px">Join Our Practice</h2>
<div class="abs copy" style="left:156px;top:1426px;width:414px">
  <p>If You're Looking For An Exceptional Dental Practice, We're Here To Help! Our Team Is Made Up Of Highly Skilled Professionals Who Are Dedicated To Ensuring That All Our Patients Receive Top-Notch Care In A Welcoming And Comfortable Environment.</p>
  <p>Whether You Need A Routine Examination Or A More Specialised Treatment, We Have All The Resources To Provide You With The Best Dental Care Possible. Our Practice Is Always Up-To-Date With The Latest Techniques And Technologies To Make Sure That Our Patients Receive The Best Possible Results.</p>
  <p>We Understand That Dental Care Can Be Expensive Which Is Why We Offer Affordable Prices To Ensure That Everyone Has Access To Quality Care. If You'd Like To Learn More About Our Practice, Please Don't Hesitate To Contact Us.</p>
</div>
<span class="abs btn" style="left:156px;top:1657px">Join Now</span>
<div class="abs ph" style="left:638px;top:1337px;width:406px;height:381px;background:linear-gradient(135deg,#d7e3ec,#8fa9c6)" role="img" aria-label="Dental team treating a patient with a microscope"></div>

<h2 class="abs section-title" style="left:0;width:1200px;text-align:center;top:1882px">Treatments</h2>
<div class="abs card yellow" style="left:156px;top:1945px"><svg width="60" height="46" viewBox="0 0 60 46"><rect x="4" y="12" width="52" height="22" rx="11" fill="#f7a8b8"/><rect x="10" y="17" width="40" height="12" rx="4" fill="#fff" stroke="#2a3f8f" stroke-width="2"/></svg><h3>Teeth Whitening</h3><p>Lorem Ipsum is simply dummy text of the printing &amp; typesetting industry.</p></div>
<div class="abs card peach" style="left:460px;top:1945px"><svg width="66" height="46" viewBox="0 0 66 46"><rect x="2" y="8" width="30" height="34" rx="3" fill="#c9d6f5" stroke="#2a3f8f" stroke-width="2"/><path d="M38 10c6-4 10 0 12 0s6-4 12 0c4 6-2 14-4 30h-4l-4-12-4 12h-4c-2-16-8-24-4-30z" fill="#fff" stroke="#2a3f8f" stroke-width="2"/></svg><h3>Dental Implant</h3><p>Lorem Ipsum is simply dummy text of the printing &amp; typesetting industry.</p></div>
<div class="abs card mint" style="left:764px;top:1945px"><svg width="46" height="46" viewBox="0 0 46 46"><path d="M6 10c6-4 10 0 12 0s6-4 12 0c4 6-2 14-4 30h-4l-4-12-4 12h-4C8 24 2 16 6 10z" fill="#fff" stroke="#2a3f8f" stroke-width="2"/><circle cx="36" cy="8" r="5" fill="#f6d365"/></svg><h3>Teeth Fillings</h3><p>Lorem Ipsum is simply dummy text of the printing &amp; typesetting industry.</p></div>
<div class="abs card peach" style="left:156px;top:2165px"><svg width="60" height="46" viewBox="0 0 60 46"><rect x="4" y="26" width="52" height="16" rx="3" fill="#fff" stroke="#2a3f8f" stroke-width="2"/><path d="M6 6h24" stroke="#2a3f8f" stroke-width="2"/><circle cx="8" cy="6" r="4" fill="#f7a8b8"/></svg><h3>Oral Surgery</h3><p>Lorem Ipsum is simply dummy text of the printing &amp; typesetting industry.</p></div>
<div class="abs card mint" style="left:460px;top:2165px"><svg width="66" height="46" viewBox="0 0 66 46"><path d="M16 6h34M16 6l4-3M16 6l4 3M50 6l-4-3M50 6l-4 3" stroke="#2a3f8f" stroke-width="2" fill="none"/><rect x="2" y="24" width="62" height="16" rx="3" fill="#b9dcf5" stroke="#2a3f8f" stroke-width="2"/></svg><h3>Crown &amp; Bridges</h3><p>Lorem Ipsum is simply dummy text of the printing &amp; typesetting industry.</p></div>
<div class="abs card yellow" style="left:764px;top:2165px"><svg width="52" height="46" viewBox="0 0 52 46"><path d="M6 12c6-4 10 0 14 0s8-4 14 0c4 6-2 14-4 28h-6l-4-12-4 12h-6C8 26 2 18 6 12z" fill="#fff" stroke="#2a3f8f" stroke-width="2"/><circle cx="44" cy="8" r="3" fill="#f6d365"/></svg><h3>Periodontal Care</h3><p>Lorem Ipsum is simply dummy text of the printing &amp; typesetting industry.</p></div>

<div class="abs" style="left:0;top:2455px;width:381px;height:394px;background:linear-gradient(160deg,#a9e4ef,#5cc4d9)" role="img" aria-label="Dentist in white coat holding dental instruments"></div>
<section class="abs testi">
  <h2>Testimonial</h2>
  <p>Lorem Ipsum is simply dummy text of the printing and typesetting industry. Lorem Ipsum has been the industry's standard dummy text ever since the 1500s, when an unknown printer took a galley of type and scrambled it to make a type specimen book. It has survived not only five centuries, but also the leap into electronic typesetting, remaining essentially unchanged.</p>
  <div class="author"><div class="avatar"></div><div><b>Willow Hart</b><small>Lorem Ipsum</small></div><div class="dots"><i></i><i></i><i class="on"></i><i></i></div></div>
</section>
<div class="abs quote-box"><svg width="58" height="44" viewBox="0 0 58 44"><path d="M2 18Q2 2 20 0v8Q12 10 12 18h14v26H2zM32 18Q32 2 50 0v8Q42 10 42 18h14v26H32z" fill="var(--navy)"/></svg></div>

<h2 class="abs section-title" style="left:156px;top:3011px">Our Team</h2>
<div class="abs copy" style="left:156px;top:3065px;width:240px"><p>We Are Delighted To Introduce You To Our Experienced And Compassionate Dental Team.</p><p>Our Team Comprises Highly Skilled Dental Professionals Who Are Dedicated To Providing You With High-Quality Dental Care Services...</p></div>
<span class="abs btn" style="left:156px;top:3197px">Read More</span>
<div class="abs team-card" style="left:463px;top:2992px"><div class="ph" role="img" aria-label="Portrait of Dr. Ada Fenwick"></div><div class="info"><small>General Dentist</small><h3>Dr. Ada Fenwick</h3><p>Lorem Ipsum is simply dummy text of the printing...</p></div></div>
<div class="abs team-card" style="left:664px;top:2992px"><div class="ph" role="img" aria-label="Portrait of Dr. Owen Carrick"></div><div class="info"><small>General Dentist</small><h3>Dr. Owen Carrick</h3><p>Lorem Ipsum is simply dummy text of the printing...</p></div></div>
<div class="abs team-card" style="left:865px;top:2992px"><div class="ph" role="img" aria-label="Portrait of Dr. Iris Pemberton"></div><div class="info"><small>General Dentist</small><h3>Dr. Iris Pemberton</h3><p>Lorem Ipsum is simply dummy text of the printing...</p></div></div>

<div class="abs map" role="img" aria-label="Map showing the practice location"></div>

<footer class="abs footer">
  <div class="abs footer-logo">BRAMBLEFORD<br><span class="sub">DENTAL PRACTICE</span></div>
  <div class="abs col" style="left:406px"><h4>Contact Us</h4>☏ 555-014-2290<br>✉ info@bramblefordpractice.com<br>⌖ Lorem Ipsum 1,<br>&nbsp;&nbsp;&nbsp;40217 Elmsworth</div>
  <div class="abs col" style="left:662px;line-height:1.75"><h4>Quick Links</h4><span style="color:var(--brand-blue)">Home</span><br>About Us<br>New Patients<br>Treatments<br>Fees<br>Contact Us</div>
  <div class="abs col" style="left:848px"><h4>Opening Hours</h4>
    <table class="hours" style="font-size:10.5px;line-height:1.75;border-collapse:collapse;color:#e7ddd2">
      <tr><td>Monday</td><td>9.00 am - 5.00 pm</td></tr><tr><td>Tuesday</td><td>9.00 am - 6.00 pm</td></tr><tr><td>Wednesday</td><td>9.00 am - 6.00 pm</td></tr><tr><td>Thursday</td><td>9.00 am - 5.30 pm</td></tr><tr><td>Friday</td><td>8.00 am - 4.00 pm</td></tr><tr><td>Saturday</td><td>By appointment</td></tr><tr><td>Sunday</td><td>Closed</td></tr>
    </table>
  </div>
</footer>
<div class="abs bottombar"><span>© 2025 Brambleford Dental Practice - All Rights Reserved.</span><div class="social"><i></i><i></i><i></i></div></div>

</body>
</html>
```